Auntie Verdict Billboard

I need a billboard designed for a Personal Injury Law firm. I need to simple not busy. I am attaching the following as suggestions to use. Need good colors that show up from Road Simple that can leave people associating injury lawyer with Auntie Verdict. Big picture of Dottie. Need Auntieverdict.com and 555-417-9038 to be big. possiblly let the emojis do the talking for personal injury and money settlement. Colors for logo should be similar to website auntieverdict.com
Updates

Billboard size. 10.5ft. X 36ft.

Target Market(s)

Car Accident Victims

Font styles to use
Sans Serif

Requirements
Must have
• Picture of Dottie. auntieverdict.com. 555-417-9038. message needs to be clear that she is a personal injury attorney. Clear simple message. Colors bold and visable to highway drivers
Should not have
• Busy ad.

```html
<!DOCTYPE html>
<html lang="en">
<head>
<meta charset="utf-8">
<title>Auntie Verdict Billboard</title>
<link rel="stylesheet" href="https://fonts.googleapis.com/css2?family=Archivo+Black&family=Open+Sans:wght@400;700;800&display=swap">
<style>
  :root {
    --stage: #4d4d4d;
    --brand-blue: #0d4f9c;
    --brand-red: #c01f2e;
    --white: #ffffff;
    --portrait-dark: #1b1d26;
    --portrait-mid: #3a3c48;
    --emoji-yellow: #f6c21c;
    --emoji-orange: #e8951a;
  }
  html, body {
    margin: 0;
    padding: 0;
    width: 1200px;
    height: 960px;
    overflow: hidden;
    background: var(--stage);
  }
  .billboard {
    position: absolute;
    left: 40px;
    top: 316px;
    width: 1120px;
    height: 327px;
    display: block;
    filter: drop-shadow(0 14px 18px rgba(0,0,0,0.45));
  }
  .panel-bg { fill: var(--brand-blue); }
  .stripe { fill: var(--white); }
  .red-field { fill: var(--brand-red); }
  .headline {
    font-family: "Archivo Black", "Arial Black", sans-serif;
    fill: var(--white);
    text-anchor: middle;
  }
  .phone-pill {
    fill: var(--brand-blue);
    stroke: var(--white);
    stroke-width: 2;
  }
  .phone-number {
    font-family: "Open Sans", Arial, sans-serif;
    font-weight: 800;
    fill: var(--white);
    text-anchor: middle;
  }
  .web-address {
    font-family: "Open Sans", Arial, sans-serif;
    font-size: 19px;
    letter-spacing: 4px;
    fill: var(--white);
    text-anchor: middle;
    font-weight: 400;
  }
  .web-address .domain { font-weight: 700; }
  .firm-name {
    font-family: "Open Sans", Arial, sans-serif;
    font-weight: 700;
    fill: var(--white);
    text-anchor: middle;
  }
  .firm-sub {
    font-family: "Open Sans", Arial, sans-serif;
    font-weight: 700;
    fill: var(--white);
    letter-spacing: 4px;
    text-anchor: middle;
  }
</style>
</head>
<body>
<svg class="billboard" viewBox="0 0 1342 392" xmlns="http://www.w3.org/2000/svg">
  <defs>
    <linearGradient id="portraitFill" x1="0" y1="0" x2="0" y2="1">
      <stop offset="0" stop-color="var(--portrait-mid)"/>
      <stop offset="1" stop-color="var(--portrait-dark)"/>
    </linearGradient>
    <radialGradient id="emojiFill" cx="0.4" cy="0.35" r="0.7">
      <stop offset="0" stop-color="var(--emoji-yellow)"/>
      <stop offset="1" stop-color="var(--emoji-orange)"/>
    </radialGradient>
  </defs>

  <rect class="panel-bg" x="0" y="0" width="1342" height="392"/>
  <polygon class="stripe" points="318,0 378,0 310,392 250,392"/>
  <polygon class="red-field" points="378,0 1100,0 975,392 310,392"/>
  <polygon class="stripe" points="1100,0 1108,0 1002,392 975,392"/>

  <path d="M30,392 L30,90 Q30,10 110,10 L270,10 Q350,10 350,90 L350,392 Z" fill="url(#portraitFill)"
        role="img" aria-label="Portrait photo of the attorney in a dark suit, smiling"/>

  <text class="headline" x="655" y="117" font-size="100">AUNTIE</text>
  <text class="headline" x="655" y="222" font-size="100">VERDICT</text>

  <rect class="phone-pill" x="357" y="247" width="595" height="85" rx="42" ry="42"/>
  <text class="phone-number" x="655" y="315" font-size="72">555-417-9038</text>

  <text class="web-address" x="657" y="364">WWW.<tspan class="domain">AUNTIEVERDICT</tspan>.COM</text>

  <circle cx="1170" cy="158" r="125" fill="url(#emojiFill)"
          role="img" aria-label="Injured emoji with a white bandage wrapped around its head"/>

  <text class="firm-name" x="1180" y="340" font-size="22">HARBOR LAW FIRM</text>
  <text class="firm-sub" x="1180" y="357" font-size="10">AUNTIE VERDICT</text>
</svg>
</body>
</html>
```